Business Card for my New Brokerage

Looking to get a business card design for my new Real Estate Brokerage.
I want it with Picture, Phone Number, Email, Website, Office Address
Name and Designation. Please add logo too.

Target Market(s)

Real Estate Investors or Home Buyers

Industry/Entity Type

Real Estate

Contact Information for Business Card

Name, Email, Phone Number, website, email, office address

Colors
EB3D1F
EC4F4E
F09395
F8D3D4
FCEDEE

Requirements
Must have
• Minimalistic, Clean, Modern, Photo
Nice to have
• White and Red Colors

```html
<!DOCTYPE html>
<html lang="en">
<head>
<meta charset="utf-8">
<title>Ember Realty Inc – Business Card</title>
<link href="https://fonts.googleapis.com/css2?family=Montserrat:wght@400;500;600;700;800&display=swap" rel="stylesheet">
<style>
  :root {
    --brand-red: #e00a0a;
    --ink: #1d1d1d;
    --ink-soft: #333333;
    --rule-grey: #c9c9c9;
    --band-grey: #c4c4c4;
    --card-white: #ffffff;
    --page: #ffffff;
    --photo-dark: #2a2a2c;
    --photo-light: #e9e4df;
  }
  * { box-sizing: border-box; margin: 0; padding: 0; }
  html, body { width: 1200px; height: 3147px; overflow: hidden; background: var(--page); }
  body { font-family: "Montserrat", sans-serif; color: var(--ink); position: relative; }

  .card {
    position: absolute;
    left: 145px;
    width: 911px;
    height: 520px;
    background: var(--card-white);
    box-shadow: 0 6px 26px rgba(0,0,0,0.16);
    overflow: hidden;
  }
  .card--front { top: 993px; }
  .card--back { top: 1633px; }

  /* front */
  .brand-name {
    position: absolute; left: 0; right: 0; top: 120px;
    text-align: center;
    font-weight: 700; font-size: 148px; letter-spacing: 2px; line-height: 1;
    color: var(--brand-red);
  }
  .brand-tagline {
    position: absolute; left: 0; right: 0; top: 272px;
    text-align: center;
    font-weight: 500; font-size: 44px; letter-spacing: 10px;
    color: var(--brand-red);
  }
  .brand-url {
    position: absolute; left: 0; right: 0; top: 398px;
    text-align: center;
    font-weight: 400; font-size: 38px; letter-spacing: 3px;
    color: var(--ink-soft);
  }
  .brand-url strong { color: var(--brand-red); font-weight: 700; }

  .band { position: absolute; bottom: 0; left: 0; width: 911px; height: 26px; }

  /* back */
  .agent-name {
    position: absolute; left: 57px; top: 82px;
    font-weight: 700; font-size: 60px; letter-spacing: 1px; line-height: 1;
    color: var(--brand-red);
  }
  .agent-role {
    position: absolute; left: 58px; top: 154px;
    font-weight: 600; font-size: 29px; letter-spacing: 3px;
    color: var(--ink);
  }
  .divider {
    position: absolute; left: 63px; top: 218px; width: 430px; height: 2px;
    background: var(--rule-grey);
  }
  .contact-list { position: absolute; left: 56px; top: 254px; list-style: none; }
  .contact-item { display: flex; align-items: flex-start; margin-bottom: 14px; }
  .contact-item svg { width: 26px; height: 26px; flex: none; margin-right: 20px; margin-top: 2px; fill: var(--brand-red); }
  .contact-item--phone { font-weight: 600; font-size: 40px; line-height: 1; }
  .contact-item--phone svg { margin-top: 8px; }
  .contact-text { font-weight: 500; font-size: 19px; letter-spacing: 1px; line-height: 1.25; color: var(--ink); }

  .agent-photo {
    position: absolute; right: 0; top: 0; width: 360px; height: 496px;
    background: linear-gradient(180deg, var(--photo-light) 0%, #b99a82 28%, var(--photo-dark) 52%, #1c1c1e 100%);
  }
</style>
</head>
<body>

<section class="card card--front">
  <div class="brand-name">EMBER</div>
  <div class="brand-tagline">REALTY INC</div>
  <div class="brand-url">www.<strong>emberrealtyinc</strong>.com</div>
  <svg class="band" viewBox="0 0 911 26" aria-hidden="true">
    <polygon points="420,13 911,13 911,26 428,26" fill="var(--band-grey)"/>
    <polygon points="0,2 402,2 412,26 0,26" fill="var(--brand-red)"/>
  </svg>
</section>

<section class="card card--back">
  <div class="agent-name">CARTER HALE</div>
  <div class="agent-role">Real Estate Brokerage</div>
  <div class="divider"></div>

  <ul class="contact-list">
    <li class="contact-item contact-item--phone">
      <svg viewBox="0 0 24 24" aria-hidden="true"><path d="M6.6 10.8a15.1 15.1 0 0 0 6.6 6.6l2.2-2.2c.3-.3.7-.4 1-.2 1.1.4 2.3.6 3.6.6.6 0 1 .4 1 1V20c0 .6-.4 1-1 1A17 17 0 0 1 3 4c0-.6.4-1 1-1h3.5c.6 0 1 .4 1 1 0 1.3.2 2.5.6 3.6.1.3 0 .7-.2 1z"/></svg>
      <span>555-0142-88</span>
    </li>
    <li class="contact-item">
      <svg viewBox="0 0 24 24" aria-hidden="true"><path d="M3 6h18v13H3z M3 6l9 7 9-7" fill="none" stroke="var(--brand-red)" stroke-width="2.4"/></svg>
      <span class="contact-text">info@emberrealtyinc.com</span>
    </li>
    <li class="contact-item">
      <svg viewBox="0 0 24 24" aria-hidden="true"><path d="M12 2a7 7 0 0 0-7 7c0 5 7 12 7 12s7-7 7-12a7 7 0 0 0-7-7zm0 9.5A2.5 2.5 0 1 1 12 6.5a2.5 2.5 0 0 1 0 5z"/></svg>
      <span class="contact-text">Lorem Ipsum is simply dummy text<br>of the printing and typesetting industry.</span>
    </li>
    <li class="contact-item">
      <svg viewBox="0 0 24 24" aria-hidden="true"><circle cx="12" cy="12" r="9" fill="none" stroke="var(--brand-red)" stroke-width="2.2"/><path d="M3 12h18M12 3c3 3 3 15 0 18M12 3c-3 3-3 15 0 18" fill="none" stroke="var(--brand-red)" stroke-width="1.8"/></svg>
      <span class="contact-text">www.emberrealtyinc.com</span>
    </li>
  </ul>

  <div class="agent-photo" role="img" aria-label="Portrait photo of the agent in a dark suit and tie"></div>

  <svg class="band" viewBox="0 0 911 26" aria-hidden="true">
    <polygon points="0,13 466,13 458,26 0,26" fill="var(--band-grey)"/>
    <polygon points="488,2 911,2 911,26 478,26" fill="var(--brand-red)"/>
  </svg>
</section>

</body>
</html>
```